Manuka Honey company needs a Upmarket, Luxury Website!

New Zealand, Taranaki based Manuka Honey company Rimu Vale Honey is looking for a new website, we are looking for an upmarket, luxury, serious website design. We export the highest quality quality Manuka Honey, straight from the Taranaki region.

Main export markets are Asia & Europe, also New Zealand & Australia.

Looking to have a beautiful, upmarket, serious, luxurious & graphical experience with mobile optimization in mind. Like the use of product staging/mockups

You can use copy from other websites to build the site and we will change the copy after the design is finished.

***Please include 'Honey Product' mockups in website.

*Will add illustrator files in coming days***

Feel free to make website functional in Shopify, Wordpress or WIX

Target Market(s)

Asia, Europe (main markets) New Zealand, Australia (Submarkets)

Coding

Coded - Design and coding required

Number of Pages Required

4 page

Requirements
Must have
• Home, Shop, About Us, Contact Us

Homepage to include:

Our Products
Company Video (video under construction)
What is MGO/KPS
Newsletter Opt-in

***(Not in Order)***

Please include 'Honey Product' mockups in website.
*Will add illustrator files in coming days
Nice to have
• FAQ & Partnership Inquiries (hyperlink in footer)

```html
<!DOCTYPE html>
<html lang="en">
<head>
<meta charset="utf-8">
<title>Rimu Vale Honey — Manuka Honey</title>
<link href="https://fonts.googleapis.com/css2?family=Montserrat:wght@400;500;600;700;800&family=Lato:wght@400;700&display=swap" rel="stylesheet">
<style>
  :root {
    --gold: #e3a516;
    --gold-deep: #d38b0b;
    --gold-soft: #e9c35a;
    --ink: #1c1c1c;
    --text: #3b3b3b;
    --muted: #666;
    --cream: #f6f1e2;
    --white: #ffffff;
    --black: #050505;
    --line: #cfcfcf;
  }
  * { box-sizing: border-box; margin: 0; padding: 0; }
  html, body { width: 1200px; height: 3497px; overflow: hidden; }
  body { position: relative; background: var(--white); font-family: "Lato", sans-serif; color: var(--text); }
  .abs { position: absolute; }
  .heading { font-family: "Montserrat", sans-serif; font-weight: 700; letter-spacing: 3px; color: var(--ink); }

  /* Header */
  .site-header { left: 0; top: 0; width: 1200px; height: 90px; background: var(--white); }
  .brand { left: 106px; top: 22px; display: flex; align-items: center; gap: 12px; font-family: "Montserrat", sans-serif; font-weight: 500; font-size: 26px; letter-spacing: 3px; color: var(--ink); }
  .brand-dot { width: 40px; height: 40px; border-radius: 50%; border: 2px solid var(--gold); }
  .main-nav { top: 36px; font-family: "Montserrat", sans-serif; font-size: 14px; font-weight: 500; color: var(--ink); letter-spacing: .5px; }
  .main-nav.active { color: var(--gold); font-weight: 600; }
  .nav-sep { top: 34px; width: 1px; height: 18px; background: var(--ink); }

  /* Hero */
  .hero { left: 0; top: 90px; width: 1200px; height: 669px; background: radial-gradient(ellipse at 70% 30%, #f3f1ee 0%, #c9d0e4 35%, #8c9a86 75%, #6f7b5e 100%); }
  .hero-badge { left: 78px; top: 191px; width: 454px; height: 454px; border-radius: 50%; background: rgba(230,167,20,.95); text-align: center; color: var(--white); }
  .hero-kicker { margin-top: 160px; font-family: "Montserrat", sans-serif; font-weight: 500; font-size: 20px; letter-spacing: 2px; }
  .hero-title { font-family: "Montserrat", sans-serif; font-weight: 800; font-size: 54px; line-height: 48px; letter-spacing: 5px; margin-top: 14px; }
  .hero-btn { display: inline-block; margin-top: 22px; width: 180px; height: 46px; border: 2px solid var(--white); border-radius: 4px; line-height: 42px; font-family: "Montserrat", sans-serif; font-weight: 700; font-size: 13px; letter-spacing: 1.5px; }
  .chevron { fill: none; stroke: #333; stroke-width: 3; }

  /* About */
  .about-media { left: 0; top: 759px; width: 608px; height: 526px; background: linear-gradient(135deg, #eeeceb 0%, #dcd6cf 45%, #c97a1a 60%, #7c8a4f 100%); }
  .play-btn { left: 293px; top: 981px; }
  .about-title { left: 685px; top: 878px; font-size: 30px; }
  .about-copy { left: 687px; top: 932px; width: 440px; font-size: 14px; line-height: 23.5px; color: var(--text); }
  .about-copy p + p { margin-top: 23px; }
  .pill { border-radius: 30px; background: linear-gradient(90deg, var(--gold-deep), var(--gold-soft)); color: var(--white); font-family: "Montserrat", sans-serif; font-weight: 700; text-align: center; letter-spacing: 1.5px; }
  .about-btn { left: 684px; top: 1125px; width: 187px; height: 50px; line-height: 50px; font-size: 13px; }

  /* Products */
  .products { left: 0; top: 1285px; width: 1200px; height: 666px; background: linear-gradient(180deg, var(--cream) 0%, #ece7d6 50%, #c9c1ab 80%, #e6e0cf 100%); }
  .products-kicker { left: 0; top: 1342px; width: 1200px; text-align: center; font-family: "Montserrat", sans-serif; font-size: 18px; letter-spacing: 2px; color: var(--ink); }
  .products-title { left: 0; top: 1366px; width: 1200px; text-align: center; font-size: 30px; }
  .products-frame { left: 111px; top: 1466px; width: 980px; height: 374px; border: 1px solid var(--line); }
  .card-divider { top: 1466px; width: 1px; height: 374px; background: var(--line); }
  .product-card { top: 1466px; width: 244px; height: 374px; text-align: center; }
  .product-card.featured { background: var(--white); top: 1448px; height: 408px; box-shadow: 0 4px 16px rgba(0,0,0,.06); }
  .jar { width: 96px; height: 175px; margin: 32px auto 0; border-radius: 14px 14px 22px 22px; background: linear-gradient(90deg, #5a2d06 0%, #1b1410 20%, #221a14 80%, #5a2d06 100%); }
  .featured .jar { margin-top: 50px; }
  .product-name { margin-top: 26px; font-family: "Montserrat", sans-serif; font-weight: 500; font-size: 19px; color: var(--ink); }
  .product-price { margin-top: 6px; font-family: "Montserrat", sans-serif; font-weight: 600; font-size: 17px; color: var(--ink); }
  .stars { color: var(--gold); letter-spacing: 1px; font-size: 14px; margin-right: 4px; }
  .card-btn { width: 149px; height: 38px; line-height: 38px; margin: 20px auto 0; font-size: 11px; color: #4a3308; }

  /* MGO / KPS */
  .mgo-title { left: 0; top: 2032px; width: 1200px; text-align: center; font-size: 30px; }
  .mgo-sub { left: 0; top: 2078px; width: 1200px; text-align: center; font-size: 15px; color: var(--muted); }
  .mgo-ring { left: 125px; top: 2185px; width: 488px; height: 488px; border-radius: 50%; border: 2px solid #d8d8d8; }
  .mgo-sun { left: 153px; top: 2212px; width: 434px; height: 434px; border-radius: 50%; background: radial-gradient(circle at 45% 40%, #f0b526, #e29a0c); }
  .mgo-jars { left: 242px; top: 2483px; width: 247px; height: 265px; border-radius: 12px; background: linear-gradient(160deg, #2a211b 0%, #0e0b09 60%, #3a2a10 100%); }
  .ring-dot { width: 14px; height: 14px; border-radius: 50%; background: var(--black); }
  .feature-icon { width: 86px; height: 86px; border-radius: 50%; border: 2px solid #e6e6e6; background: var(--white); display: flex; align-items: center; justify-content: center; }
  .feature { font-family: "Montserrat", sans-serif; color: var(--ink); }
  .feature-label { font-size: 17px; letter-spacing: 2px; font-weight: 400; }
  .feature-name { font-size: 17px; letter-spacing: 2px; font-weight: 700; }
  .feature-desc { font-family: "Lato", sans-serif; font-size: 13px; color: var(--muted); margin-top: 4px; }

  /* Newsletter */
  .newsletter { left: 0; top: 2842px; width: 1200px; height: 408px; background: linear-gradient(180deg, #6f7d89 0%, #8e9598 30%, #4a4a3e 55%, #3c5a22 75%, #4d7a2a 100%); }
  .news-title { left: 0; top: 2956px; width: 1200px; text-align: center; font-size: 30px; color: var(--white); letter-spacing: 4px; }
  .news-sub { left: 0; top: 3004px; width: 1200px; text-align: center; font-size: 15px; color: var(--white); }
  .news-form { left: 313px; top: 3047px; width: 556px; height: 51px; background: var(--white); }
  .news-input { left: 348px; top: 3064px; font-size: 14px; color: #555; }
  .news-btn { left: 708px; top: 3052px; width: 155px; height: 41px; line-height: 41px; background: linear-gradient(90deg, var(--gold-deep), var(--gold)); color: var(--white); font-family: "Montserrat", sans-serif; font-weight: 700; font-size: 14px; letter-spacing: 1.5px; text-align: center; }

  /* Footer */
  .footer { left: 0; top: 3250px; width: 1200px; height: 247px; background: var(--black); border-top: 4px solid var(--white); }
  .footer-arch { left: 510px; top: 3176px; width: 164px; height: 164px; border-radius: 50%; background: var(--black); border: 4px solid var(--white); }
  .footer-seal { left: 532px; top: 3198px; width: 120px; height: 120px; border-radius: 50%; border: 1.5px solid #7a6a3a; display: flex; align-items: center; justify-content: center; text-align: center; font-family: "Montserrat", sans-serif; font-weight: 600; font-size: 13px; letter-spacing: 1.5px; color: var(--gold); line-height: 18px; }
  .footer-link { top: 3364px; font-family: "Montserrat", sans-serif; font-weight: 500; font-size: 13px; color: var(--gold); }
  .copyright { left: 0; top: 3403px; width: 1200px; text-align: center; font-size: 11px; color: #cfcfcf; letter-spacing: .3px; }
  .social { top: 3437px; width: 14px; height: 14px; border-radius: 50%; background: var(--gold); }
</style>
</head>
<body>

<header class="abs site-header">
  <div class="abs brand"><span class="brand-dot"></span>RIMU VALE HONEY</div>
  <span class="abs main-nav active" style="left:565px">HOME</span>
  <span class="abs nav-sep" style="left:661px"></span>
  <span class="abs main-nav" style="left:698px">SHOP</span>
  <span class="abs nav-sep" style="left:789px"></span>
  <span class="abs main-nav" style="left:820px">ABOUT US</span>
  <span class="abs nav-sep" style="left:937px"></span>
  <span class="abs main-nav" style="left:972px">CONTACT US</span>
</header>

<section class="abs hero" role="img" aria-label="Photo of a bee on white manuka blossoms"></section>
<svg class="abs" style="left:46px;top:378px" width="26" height="46"><polyline class="chevron" points="22,2 4,23 22,44"/></svg>
<svg class="abs" style="left:1118px;top:378px" width="26" height="46"><polyline class="chevron" points="4,2 22,23 4,44"/></svg>
<div class="abs hero-badge">
  <div class="hero-kicker">WELCOME TO RIMU VALE HONEY</div>
  <div class="hero-title">MANUKA<br>HONEY</div>
  <div class="hero-btn">VIEW PRODUCT</div>
</div>

<section>
  <div class="abs about-media" role="img" aria-label="Bowl of manuka honey with a wooden dipper beside flowering manuka branches"></div>
  <svg class="abs play-btn" width="74" height="74" viewBox="0 0 74 74">
    <circle cx="37" cy="37" r="34" fill="none" stroke="#fff" stroke-width="4"/>
    <polygon points="29,22 54,37 29,52" fill="#fff"/>
  </svg>
  <h2 class="abs heading about-title">ABOUT OUR COMPANY</h2>
  <div class="abs about-copy">
    <p>Lorem Ipsum is simply dummy text of the printing and typeset-ting industry. Lorem Ipsum has been the industry's standard dummy text ever since the 1500s, when an unknown printer took a galley of type and scrambled it to make</p>
    <p>was popularised in the 1960s with the release of Letraset sheets containing Lorem Ipsum passages, and more recently</p>
  </div>
  <div class="abs pill about-btn">LEARN MORE</div>
</section>

<section>
  <div class="abs products" role="img" aria-label="Soft misty view of a snow-capped mountain over farmland"></div>
  <div class="abs products-kicker">OUR PRODUCTS</div>
  <h2 class="abs heading products-title">FEATURED PRODUCTS</h2>
  <div class="abs products-frame"></div>
  <div class="abs card-divider" style="left:846px"></div>
  <svg class="abs" style="left:64px;top:1610px" width="22" height="36"><polyline class="chevron" points="19,2 3,18 19,34" stroke="#888"/></svg>
  <svg class="abs" style="left:1112px;top:1610px" width="22" height="36"><polyline class="chevron" points="3,2 19,18 3,34" stroke="#888"/></svg>

  <div class="abs product-card" style="left:116px">
    <div class="jar" role="img" aria-label="Jar of manuka honey"></div>
    <div class="product-name">Mounka Honey</div>
    <div class="product-price"><span class="stars">★★★★★</span>USD $18.00</div>
    <div class="pill card-btn">LEARN MORE</div>
  </div>
  <div class="abs product-card featured" style="left:354px">
    <div class="jar" role="img" aria-label="Jar of manuka honey"></div>
    <div class="product-name">Mounka Honey</div>
    <div class="product-price"><span class="stars">★★★★★</span>USD $18.00</div>
    <div class="pill card-btn">LEARN MORE</div>
  </div>
  <div class="abs product-card" style="left:610px">
    <div class="jar" role="img" aria-label="Jar of manuka honey"></div>
    <div class="product-name">Mounka Honey</div>
    <div class="product-price"><span class="stars">★★★★★</span>USD $18.00</div>
    <div class="pill card-btn">LEARN MORE</div>
  </div>
  <div class="abs product-card" style="left:847px">
    <div class="jar" role="img" aria-label="Jar of manuka honey"></div>
    <div class="product-name">Mounka Honey</div>
    <div class="product-price"><span class="stars">★★★★★</span>USD $18.00</div>
    <div class="pill card-btn">LEARN MORE</div>
  </div>
</section>

<section>
  <h2 class="abs heading mgo-title">WHAT IS MGO/KPS</h2>
  <p class="abs mgo-sub">Lorem Ipsum is simply dummy text of the printing and typesetting industry.</p>
  <div class="abs mgo-ring"></div>
  <div class="abs mgo-sun"></div>
  <div class="abs mgo-jars" role="img" aria-label="Two jars of premium manuka honey"></div>
  <div class="abs ring-dot" style="left:526px;top:2240px"></div>
  <div class="abs ring-dot" style="left:593px;top:2341px"></div>
  <div class="abs ring-dot" style="left:606px;top:2458px"></div>
  <div class="abs ring-dot" style="left:572px;top:2557px"></div>

  <div class="abs feature-icon" style="left:564px;top:2166px">
    <svg width="44" height="40" viewBox="0 0 44 40" fill="none" stroke="#e3a516" stroke-width="2">
      <polygon points="11,2 19,6 19,15 11,19 3,15 3,6"/><polygon points="27,2 35,6 35,15 27,19 19,15 19,6"/><polygon points="19,16 27,20 27,29 19,33 11,29 11,20"/><polygon points="35,16 43,20 43,29 35,33 27,29 27,20"/>
    </svg>
  </div>
  <div class="abs feature" style="left:668px;top:2165px">
    <div class="feature-label">CERTIFIED KPS</div>
    <div class="feature-name">SUPER PREIMUM</div>
    <div class="feature-desc">Lorem ipsum dolor sit amet, consectetur adipiscing elit, sed do ei</div>
  </div>

  <div class="abs feature-icon" style="left:648px;top:2292px">
    <svg width="36" height="40" viewBox="0 0 36 40" fill="none" stroke="#e3a516" stroke-width="2">
      <rect x="8" y="3" width="20" height="6" rx="2"/><rect x="4" y="9" width="28" height="28" rx="8"/><circle cx="18" cy="23" r="5"/>
    </svg>
  </div>
  <div class="abs feature" style="left:746px;top:2292px">
    <div class="feature-label">CERTIFIED KPS</div>
    <div class="feature-name">ULTRA PREIMUM</div>
    <div class="feature-desc">Lorem ipsum dolor sit amet, consectetur adipiscing elit, se</div>
  </div>

  <div class="abs feature-icon" style="left:660px;top:2424px">
    <svg width="36" height="36" viewBox="0 0 36 36" fill="none" stroke="#e3a516" stroke-width="2">
      <circle cx="18" cy="18" r="14"/><circle cx="18" cy="18" r="6"/>
    </svg>
  </div>
  <div class="abs feature" style="left:756px;top:2427px">
    <div class="feature-label">CERTIFIED KPS</div>
    <div class="feature-name">SUPER PREIMUM</div>
    <div class="feature-desc">Lorem ipsum dolor sit amet, consectetur adipiscing elit,</div>
  </div>

  <div class="abs feature-icon" style="left:612px;top:2553px">
    <svg width="36" height="40" viewBox="0 0 36 40" fill="none" stroke="#e3a516" stroke-width="2">
      <circle cx="18" cy="16" r="13"/><polyline points="11,16 16,21 25,11"/><polyline points="11,27 8,38 18,34 28,38 25,27"/>
    </svg>
  </div>
  <div class="abs feature" style="left:717px;top:2573px">
    <div class="feature-label">CERTIFIED KPS</div>
    <div class="feature-name">SUPER PREIMUM</div>
    <div class="feature-desc">Lorem ipsum dolor sit amet, consectetur adipiscing elit,</div>
  </div>
</section>

<section>
  <div class="abs newsletter" role="img" aria-label="Snow-capped mountain above green pastures and trees"></div>
  <h2 class="abs heading news-title">SIGN UP FOR OUR NEWSLETTER</h2>
  <p class="abs news-sub">Lorem Ipsum is simply dummy text of the printing and typesetting</p>
  <div class="abs news-form"></div>
  <span class="abs news-input">Enter Your Email address</span>
  <div class="abs news-btn">SUBSCRIBE</div>
</section>

<footer>
  <div class="abs footer"></div>
  <div class="abs footer-arch"></div>
  <div class="abs footer-seal">RIMU VALE<br>HONEY</div>
  <span class="abs footer-link" style="left:208px">HOME</span>
  <span class="abs footer-link" style="left:322px">SHOP</span>
  <span class="abs footer-link" style="left:434px">ABOUT US</span>
  <span class="abs footer-link" style="left:574px">FAQ</span>
  <span class="abs footer-link" style="left:673px">PARTNERSHIP INQUIRIES</span>
  <span class="abs footer-link" style="left:906px">CONTACT US</span>
  <p class="abs copyright">COPYRIGHT © 2021 RIMU VALE HONEY | ALL RIGHT RESERVED</p>
  <span class="abs social" style="left:538px"></span>
  <span class="abs social" style="left:582px"></span>
  <span class="abs social" style="left:627px"></span>
</footer>

</body>
</html>
```